Velqar Australia Pty Ltd - Stationary design

We need letterheads for hard copy print and e-copy word docs, envelopes - landscape and A3, business cards, With compliment slips and a gloss presentation folder to hold up to 20 A4 pages
Would also like to know what font and size would be recommended to suit our brand.
Logo, Colours, Brand and image can be viewed on www.velqar.com.au

Target Market(s)

Those in pain from 30yrs to 80yrs

Industry/Entity Type

Landscape

Requirements
Must have
• Logo as per trademarked logo on web site
Nice to have
• same colours as our web site logo and design
Should not have
• anything looking cheap or too common
text and font needs to be easy to read but very professional in appearance

```html
<!DOCTYPE html>
<html lang="en">
<head>
<meta charset="utf-8">
<title>Velqar Australia – Letterhead Options</title>
<link rel="stylesheet" href="https://fonts.googleapis.com/css2?family=Source+Sans+3:wght@300;400;600;700&display=swap">
<style>
  :root {
    --backdrop: #2b2b2b;
    --paper-top: #ffffff;
    --paper-bottom: #e6e6e6;
    --brand-navy: #1f3766;
    --brand-sky: #1aa7e1;
    --footer-text: #ffffff;
    --label: #ffffff;
  }
  * { margin: 0; padding: 0; box-sizing: border-box; }
  html, body {
    width: 1200px; height: 726px; overflow: hidden;
    background: var(--backdrop);
    font-family: "Source Sans 3", "Myriad Pro", Arial, sans-serif;
  }
  .stage { position: relative; width: 1200px; height: 726px; }
  .letterhead {
    position: absolute; top: 38px; width: 476px; height: 614px;
    background: linear-gradient(160deg, var(--paper-top) 40%, var(--paper-bottom) 100%);
    box-shadow: 0 2px 8px rgba(0,0,0,.45);
  }
  .letterhead--one { left: 106px; }
  .letterhead--two { left: 654px; }
  .letterhead__rule {
    position: absolute; left: 12px; top: 43px; width: 300px; height: 2px;
    background: var(--brand-sky);
  }
  .letterhead__brand {
    position: absolute; right: 34px; top: 12px;
    display: flex; align-items: center; gap: 6px;
    font-weight: 700; font-size: 30px; line-height: 1; color: var(--brand-navy);
    letter-spacing: -0.5px;
  }
  .letterhead__brand-dot {
    width: 10px; height: 10px; border-radius: 50%; background: var(--brand-navy);
  }
  .letterhead__footer {
    position: absolute; left: 0; right: 0; bottom: 0; height: 32px;
  }
  .footer__stripe {
    height: 3px; border-top: 1px solid var(--brand-sky); border-bottom: 1px solid var(--brand-sky);
    margin-bottom: 2px;
  }
  .footer__band {
    height: 27px; background: var(--brand-navy); color: var(--footer-text);
    display: flex; flex-direction: column; align-items: center; justify-content: center;
    gap: 4px; font-size: 7.4px; line-height: 1;
  }
  .footer__contacts { display: flex; gap: 5px; align-items: center; }
  .footer__item { display: inline-flex; align-items: center; gap: 2px; }
  .footer__item svg { width: 7px; height: 7px; fill: none; stroke: var(--footer-text); stroke-width: 1.4; }
  .footer__address { display: flex; gap: 5px; align-items: center; }
  .footer__company { font-weight: 700; }
  .footer__divider { width: 1px; height: 8px; background: var(--footer-text); opacity: .8; }
  .option-label {
    position: absolute; top: 672px; width: 476px; text-align: center;
    font-weight: 300; font-size: 36px; line-height: 44px; color: var(--label);
  }
  .option-label--one { left: 92px; }
  .option-label--two { left: 640px; }
</style>
</head>
<body>
<main class="stage">

  <section class="letterhead letterhead--one" aria-label="Letterhead option 1">
    <div class="letterhead__rule"></div>
    <div class="letterhead__brand"><span class="letterhead__brand-dot"></span>Velqar</div>
    <footer class="letterhead__footer">
      <div class="footer__stripe"></div>
      <div class="footer__band">
        <div class="footer__contacts">
          <span class="footer__item"><svg viewBox="0 0 10 10"><path d="M2 1l2 2-1 1.5q1 2 2.5 2.5L7 6l2 2-1.5 1.5Q2 8.5 .5 2.5z"/></svg>1300 555 018</span>
          <span class="footer__item"><svg viewBox="0 0 10 10"><rect x="1" y="2.5" width="8" height="5.5"/><path d="M1 2.5l4 3 4-3"/></svg>admin@velqar.com.au</span>
          <span class="footer__item"><svg viewBox="0 0 10 10"><circle cx="5" cy="5" r="4"/><path d="M1 5h8M5 1q-2.5 4 0 8M5 1q2.5 4 0 8"/></svg>velqar.com.au</span>
        </div>
        <div class="footer__address">
          <span class="footer__company">Velqar Australia Pty Ltd</span>
          <span class="footer__divider"></span>
          <span>Unit 12/40 Marlow Street, Corrin Vale, Qld 4999, Australia</span>
        </div>
      </div>
    </footer>
  </section>

  <section class="letterhead letterhead--two" aria-label="Letterhead option 2">
    <div class="letterhead__brand"><span class="letterhead__brand-dot"></span>Velqar</div>
    <footer class="letterhead__footer">
      <div class="footer__stripe"></div>
      <div class="footer__band">
        <div class="footer__contacts">
          <span class="footer__item"><svg viewBox="0 0 10 10"><path d="M2 1l2 2-1 1.5q1 2 2.5 2.5L7 6l2 2-1.5 1.5Q2 8.5 .5 2.5z"/></svg>1300 555 018</span>
          <span class="footer__item"><svg viewBox="0 0 10 10"><rect x="1" y="2.5" width="8" height="5.5"/><path d="M1 2.5l4 3 4-3"/></svg>admin@velqar.com.au</span>
          <span class="footer__item"><svg viewBox="0 0 10 10"><circle cx="5" cy="5" r="4"/><path d="M1 5h8M5 1q-2.5 4 0 8M5 1q2.5 4 0 8"/></svg>velqar.com.au</span>
        </div>
        <div class="footer__address">
          <span class="footer__company">Velqar Australia Pty Ltd</span>
          <span class="footer__divider"></span>
          <span>Unit 12/40 Marlow Street, Corrin Vale, Qld 4999, Australia</span>
        </div>
      </div>
    </footer>
  </section>

  <p class="option-label option-label--one">Option-1</p>
  <p class="option-label option-label--two">Option-2</p>

</main>
</body>
</html>
```